Systems and Technology Consultants - Website

Design & Build a website for a new company which operates in the Systems and Technology space for Transportation, Government and Commercial sectors.

Overall design should be minimalist in nature.
Should also have a feed that provides news and event updates on the main page.
Logo has already been awarded and should be incorporated into the site.

We like the overall layout, functionality and simplicity of the below sites. Submitted designs could be similar to or a combination of the aspects on these sites, or perhaps a whole different concept - we are open to new ideas.
Norvique.com
Teblo.it

Update 1 Dated 27 May 2014

All I am moving away from the Teblo.it website and would like it to be more aligned with Norvique.com not only in layout but in functionality. I will be extending the deadline of this design brief for two weeks to incorporate additional requirements and will add addtional funding to the project.

Apologies for not having more information available to provide but with so many submissions its getting confusing.

Thanks Derek

Please note that the brief has been updated and the deadline has been extended.

Important: We will need two language versions of the website, English and Arabic; the website is hosted on HostPelican

Hello All, Thank you for your submissions. We have narrowed it down to the final 6 designers and I just wanted to take a moment and provide a bit of feedback regarding the concepts that we like and the modifications we are looking for. First, let me mention some of the design functions we like. - At the top of the homepage we really like the "region" or "language" tab so that the website can be viewed in both English and Arabic. - We like the homepage to have clear color variation so that the different sections of the homepage are distinct. Additionally, we like the bottom portion of the homepage to be in red. We feel that draws attention to our contact information. Again, we would like the colors to integrate black, gray-scale, red, etc. - Having a search tab at the top of the home page, or integrated into the main image, so that the site is easy to navigate. - We especially like the main image to have the scrolling tabs at the bottom so it is easy to browse the services offered (Consultancy, Solutions Architecture, Masters Systems Integration, Independent Design Review). - In regards to the services offered tab we really like the idea that a few people presented that have the outside of our logo with an icon in the middle of consultancy, solutions, etc., etc. Secondly, as mentioned in our brief we really enjoy the design of norvique site. Specially, we enjoy the strong iconic images they use, the way the tabs at the top scroll easily, and contact us page that generates an email. Lastly, I've included some photos of the concept we have been working on. What we are trying to demonstrate is how our company offers a range of services that are essentially linked together. We provide individual services that when combined present the full service package. We would like this concept to be integrated into the over concept of our website. Please feel free to ask for clarification of any of the above points or contact us if you have any additional questions. We appreciate all of your hard work and are very excited to see the updated designs. Best, Marta Vennick Quelbrant Senior Program Manager marta.vennick@quelbrant-example.com

Industry/Entity Type

Government

Font styles to use
Serif
Sans Serif

Requirements
Must have
• Must work on/adapt to various/mobile devices (responsive)
Must be simple and straightforward
Colors should be in line/matching with logo
2 language versions: English and Arabic (no Thai)
Services should be the first group/row of items after/below the main image
Note: the website will be hosted by hostpelican
Nice to have
• Submit feedback form
What's New section
The banner at the bottom of the site should not be too large; we would like a narrow one more
It would be nice if the header/top banner (with Home, About, etc. tabs) could stay in place as you scroll down (like Norvique and Chatterloop)
We will likely only use one image with a Company slogan on the Home page rather than a carousel of images to rotate through
Should not have
• This is the existing website: http://www.quelbrant-example.org
We do not like the animation, the way the banner icons/titles bounce
Not simple enough, we don't like the functionality or how pages load so slowly
We do not like the logo centered - it should be at the left
The banner and its tabs should not be towards the right, we would like them to be centered, to go all the way across and to be below the logo

```html
<!DOCTYPE html>
<html lang="en">
<head>
<meta charset="utf-8">
<title>Quelbrant – Systems and Technology Consultants</title>
<link href="https://fonts.googleapis.com/css2?family=Open+Sans:wght@400;600;700&display=swap" rel="stylesheet">
<style>
:root{
  --red:#e5262b;
  --red-dark:#c21d22;
  --ink:#2b2b2b;
  --text:#666;
  --muted:#999;
  --line:#e3e3e3;
  --hero-a:#e9e4dc;
  --hero-b:#d6cfc4;
  --bar:#2f2f2f;
  --footer:#3a3a3a;
  --footer-deep:#2a2a2a;
  --white:#fff;
}
*{box-sizing:border-box;margin:0;padding:0}
html,body{width:807px;height:1200px;overflow:hidden}
body{font-family:"Open Sans",Arial,sans-serif;color:var(--text);background:var(--white);position:relative}

.site-header{height:56px;position:relative;border-bottom:1px solid var(--line)}
.brand{position:absolute;left:24px;top:12px;display:flex;align-items:center;gap:7px}
.brand-mark{width:22px;height:22px;background:var(--red)}
.brand-name{font-size:15px;font-weight:700;color:var(--red);letter-spacing:.5px}
.call{position:absolute;right:24px;top:10px;font-size:14px;font-weight:700;color:var(--red)}
.main-nav{position:absolute;left:305px;top:32px;display:flex;gap:4px}
.main-nav a{font-size:10px;color:var(--ink);text-decoration:none;padding:4px 10px}
.main-nav a.active{background:var(--red);color:var(--white)}

.hero{height:344px;position:relative;background:linear-gradient(160deg,var(--hero-a),var(--hero-b))}
.hero-copy{position:absolute;left:72px;top:100px;width:330px}
.hero-copy p{font-size:14px;line-height:1.55;color:var(--ink)}
.hero-copy strong{font-weight:700}
.btn{display:inline-block;margin-top:14px;background:var(--red);color:var(--white);font-size:10px;font-weight:600;padding:6px 12px;text-decoration:none}
.hero-image{position:absolute;left:420px;top:50px;width:330px;height:250px;background:linear-gradient(150deg,#4f5861,#aeb4ba 55%,#d9d6d0)}

.section-title{text-align:center;font-size:17px;font-weight:600;color:var(--ink);margin-top:42px}
.section-title::after{content:"";display:block;width:60px;height:1px;background:var(--line);margin:10px auto 0}

.services{display:grid;grid-template-columns:repeat(3,220px);column-gap:14px;row-gap:14px;margin:20px 0 0 70px}
.service{padding:8px 8px 10px}
.service.featured{border:1px solid var(--line);box-shadow:0 1px 4px rgba(0,0,0,.08)}
.service h3{display:flex;align-items:center;gap:7px;font-size:12px;font-weight:400;color:var(--ink);margin-bottom:5px}
.service.featured h3{color:var(--red)}
.service svg{width:18px;height:18px}
.service p{font-size:8px;line-height:1.45;color:var(--muted)}

.updates{display:grid;grid-template-columns:290px 310px;column-gap:60px;margin:34px 0 0 72px}
.col-title{font-size:15px;color:#aaa;font-weight:400;border-bottom:1px solid var(--line);padding-bottom:5px;margin-bottom:12px}
.news-item{display:flex;gap:10px;padding:6px 0 8px;border-bottom:1px solid var(--line);margin-bottom:8px}
.date{width:34px;text-align:center;color:var(--white);flex:none}
.date b{display:block;background:var(--ink);font-size:12px;padding:2px 0}
.date span{display:block;background:var(--red);font-size:9px;padding:1px 0}
.news-item h4{font-size:10px;font-weight:600;color:var(--ink)}
.news-item p{font-size:8px;line-height:1.4;color:var(--muted);margin-top:3px}

.acc-row{display:flex;justify-content:space-between;align-items:center;background:var(--bar);color:var(--white);font-size:9px;height:20px;padding-left:8px;margin-bottom:8px}
.acc-row.open{background:var(--red-dark);margin-bottom:0}
.acc-row i{width:20px;height:20px;background:var(--red);font-style:normal;font-size:14px;line-height:20px;text-align:center}
.acc-row.open i{background:var(--ink)}
.acc-body{font-size:8px;line-height:1.45;color:var(--muted);border:1px solid var(--line);border-top:0;padding:8px;margin-bottom:8px}

.site-footer{position:absolute;left:0;top:990px;width:807px;height:190px;background:var(--footer);color:#bbb}
.footer-cols{display:grid;grid-template-columns:230px 108px 148px 180px;margin:28px 0 0 72px}
.footer-cols h5{font-size:12px;font-weight:400;color:var(--white);margin-bottom:10px}
.footer-cols p,.footer-cols li{font-size:8px;line-height:1.6;list-style:none}
.footer-cols .about p{width:190px}
.map{width:170px;height:110px;background:linear-gradient(135deg,#e6e2d8,#cfd6cc)}
.copyright{position:absolute;left:0;top:1180px;width:807px;height:20px;background:var(--footer-deep);color:#999;font-size:8px;text-align:center;line-height:20px}
</style>
</head>
<body>
<header class="site-header">
  <div class="brand"><span class="brand-mark"></span><span class="brand-name">Quelbrant</span></div>
  <div class="call">Call: +100 555 0142</div>
  <nav class="main-nav">
    <a class="active" href="#">HOME</a><a href="#">Business Units</a><a href="#">Services</a><a href="#">About Us</a><a href="#">Locations</a><a href="#">Contact Us</a>
  </nav>
</header>

<section class="hero">
  <div class="hero-copy">
    <p><strong>Quelbrant Specializes</strong> in delivering quality Professional Services and Technical Projects that Support larger Business goals.</p>
    <a class="btn" href="#">Read More</a>
  </div>
  <div class="hero-image" role="img" aria-label="Photograph of a desktop monitor showing a business professional with a network of technology icons"></div>
</section>

<h2 class="section-title">Our Services</h2>
<div class="services">
  <div class="service"><h3><svg viewBox="0 0 20 20"><circle cx="10" cy="6" r="4" fill="#333"/><path d="M2 19c0-5 4-7 8-7s8 2 8 7z" fill="#333"/></svg>Consulting</h3><p>Lorem ipsum dolor sit amet, consectetur adipiscing elit sed do eiusmod tempor incididunt ut labore et dolore magna aliqua ut enim ad minim veniam quis nostrud.</p></div>
  <div class="service featured"><h3><svg viewBox="0 0 20 20"><rect x="2" y="4" width="16" height="12" rx="1" fill="#e5262b"/><rect x="5" y="7" width="10" height="2" fill="#fff"/></svg>Engineering</h3><p>Lorem ipsum dolor sit amet, consectetur adipiscing elit sed do eiusmod tempor incididunt ut labore et dolore magna aliqua ut enim ad minim veniam quis nostrud.</p></div>
  <div class="service"><h3><svg viewBox="0 0 20 20"><rect x="4" y="3" width="12" height="16" fill="#333"/><rect x="7" y="6" width="2" height="2" fill="#fff"/><rect x="11" y="6" width="2" height="2" fill="#fff"/><rect x="7" y="10" width="2" height="2" fill="#fff"/><rect x="11" y="10" width="2" height="2" fill="#fff"/></svg>Construction</h3><p>Lorem ipsum dolor sit amet, consectetur adipiscing elit sed do eiusmod tempor incididunt ut labore et dolore magna aliqua ut enim ad minim veniam quis nostrud.</p></div>
  <div class="service"><h3><svg viewBox="0 0 20 20"><path d="M4 2h9l3 3v13H4z" fill="#333"/><rect x="7" y="8" width="6" height="1.5" fill="#fff"/><rect x="7" y="11" width="6" height="1.5" fill="#fff"/></svg>Caboris nisi</h3><p>Lorem ipsum dolor sit amet, consectetur adipiscing elit sed do eiusmod tempor incididunt ut labore et dolore magna aliqua ut enim ad minim veniam quis nostrud.</p></div>
  <div class="service"><h3><svg viewBox="0 0 20 20"><circle cx="10" cy="10" r="8" fill="#333"/><circle cx="10" cy="10" r="3" fill="#fff"/></svg>Excepteur sint</h3><p>Lorem ipsum dolor sit amet, consectetur adipiscing elit sed do eiusmod tempor incididunt ut labore et dolore magna aliqua ut enim ad minim veniam quis nostrud.</p></div>
  <div class="service"><h3><svg viewBox="0 0 20 20"><path d="M10 2l7 5v11H3V7z" fill="#333"/><rect x="8" y="12" width="4" height="6" fill="#fff"/></svg>Deserunt mollit</h3><p>Lorem ipsum dolor sit amet, consectetur adipiscing elit sed do eiusmod tempor incididunt ut labore et dolore magna aliqua ut enim ad minim veniam quis nostrud.</p></div>
</div>

<div class="updates">
  <section class="news">
    <h3 class="col-title">News</h3>
    <article class="news-item"><div class="date"><b>27</b><span>Feb</span></div><div><h4>Lorem ipsum dolor sit amet,</h4><p>Lorem Ipsum is simply dummy text of the printing and typesetting industry.</p></div></article>
    <article class="news-item"><div class="date"><b>26</b><span>Feb</span></div><div><h4>Lorem ipsum dolor sit amet,</h4><p>Lorem Ipsum is simply dummy text of the printing and typesetting industry.</p></div></article>
    <article class="news-item"><div class="date"><b>28</b><span>Feb</span></div><div><h4>Lorem ipsum dolor sit amet,</h4><p>Lorem Ipsum is simply dummy text of the printing and typesetting industry.</p></div></article>
  </section>
  <section class="articles">
    <h3 class="col-title">Articles</h3>
    <div class="acc-row open">Lorem ipsum dolor sit amet, consectetur adipiscing elit<i>–</i></div>
    <div class="acc-body">Lorem ipsum dolor sit amet, consectetur adipiscing elit sed do eiusmod tempor incididunt ut labore et dolore magna aliqua. Ut enim ad minim veniam, quis nostrud exercitation ullamco laboris nisi ut aliquip ex ea commodo consequat duis aute irure.</div>
    <div class="acc-row">Lorem ipsum dolor sit amet, consectetur<i>+</i></div>
    <div class="acc-row">Lorem ipsum dolor sit amet, consectetur adipiscing elit<i>+</i></div>
  </section>
</div>

<footer class="site-footer">
  <div class="footer-cols">
    <div class="about"><h5>About Us</h5><p>Lorem ipsum dolor sit amet, consectetur adipiscing elit sed do eiusmod tempor incididunt ut labore et dolore magna aliqua ut enim ad minim veniam quis nostrud exercitation ullamco laboris.</p></div>
    <div><h5>Site Map</h5><ul><li>Home</li><li>Business Units</li><li>Services</li><li>About Us</li><li>Locations</li><li>Contact Us</li></ul></div>
    <div><h5>Get in touch</h5><p>Toll Free: +100 555 0142<br>Local: +100 555 0187<br>Fax: +100 555 0163</p></div>
    <div><h5>Map</h5><div class="map" role="img" aria-label="Street map showing the office location"></div></div>
  </div>
</footer>
<div class="copyright">Copyright © 2014 Quelbrant. All rights reserved.</div>
</body>
</html>
```